Clendora Hand Sanitizer One Page Website

I need someone to make a one page website for us. The site is www.clendora-example.com. I quickly created a simple basic page with all the elements (text, picture, table of pricing, pdf links) needed. I need someone to make the webpage look nice, professioonal, and responsive. There are only 2 links on the page pointing to two pdf files, otherwise there is no navigation needed. The product is a hand sanitizer.
Target Market(s)
Government, corporations, hospitals, large companies
Number of Pages Required
1 page
Requirements
Nice to have
- A hero image relating to hand sanitizer products would be really nice
We would like the bulleted items (Active Ingredient 75% Isopropyl Alcohol, etc) to somehow incorporate icons like the attached picture.

```html
<!DOCTYPE html>
<html lang="en">
<head>
<meta charset="utf-8">
<title>Clendora Hand Sanitizer</title>
<link rel="stylesheet" href="https://fonts.googleapis.com/css2?family=Karla:wght@700;800&family=Open+Sans:wght@400&family=Roboto:wght@400;500;700&display=swap">
<style>
:root{
  --blue:#1693cd;
  --ink:#3a3a3a;
  --muted:#555;
  --row-alt:#f4f4f4;
  --footer:#ececec;
}
*{box-sizing:border-box;margin:0;padding:0}
html,body{width:1025px;height:1200px;overflow:hidden;background:#fff}
.page{position:relative;width:1025px;height:1200px;font-family:"Open Sans",sans-serif;color:var(--ink)}
.hero{position:absolute;left:0;top:0;width:1025px;height:649px;
  background:linear-gradient(180deg,#f4f7f1 0%,#e6efdc 35%,#eef2ea 50%,#f1ece4 52%,#f6f2ec 100%)}
.brand{position:absolute;left:97px;top:34px;display:flex;align-items:center;gap:10px;
  font-family:"Karla",sans-serif;font-weight:800;font-size:40px;color:var(--ink);letter-spacing:.5px}
.brand-dot{width:30px;height:30px;border-radius:50%;background:var(--blue)}
.headline{position:absolute;left:100px;top:206px;font-family:"Karla",sans-serif;font-weight:800;font-size:32px;line-height:42px;color:var(--ink);letter-spacing:.6px}
.headline .accent{color:var(--blue)}
.features{position:absolute;left:100px;top:353px;list-style:none;width:440px}
.features li{position:relative;padding-left:23px;font-size:14px;line-height:16.5px;margin-bottom:16px;color:#222}
.features svg{position:absolute;left:0;top:1px;width:15px;height:15px}
.product-shot{position:absolute;left:560px;top:115px;width:310px;height:455px;border-radius:40px 40px 60px 60px;
  background:linear-gradient(180deg,#b5b9c1 0%,#9ea2ab 55%,#8d9199 100%)}
.nav-arrow{position:absolute;top:322px;width:22px;height:34px}
.nav-prev{left:42px}
.nav-next{right:16px}
.family-photo{position:absolute;left:640px;top:649px;width:385px;height:484px;
  background:linear-gradient(90deg,rgba(255,255,255,1) 0%,#dfe7ee 25%,#c9b8a8 55%,#d9cbbf 100%)}
.pricing{position:absolute;left:100px;top:713px;width:561px;table-layout:fixed;border-collapse:collapse;font-family:"Roboto",sans-serif;background:#fff;box-shadow:0 1px 4px rgba(0,0,0,.08)}
.pricing th{background:var(--blue);color:#fff;font-weight:700;font-size:12px;line-height:14px;text-align:left;height:57px;vertical-align:middle;white-space:nowrap}
.pricing td{font-size:12.5px;color:var(--muted);height:41px;vertical-align:middle;white-space:nowrap}
.pricing .c-container{padding-left:28px}
.pricing .c-qty{padding-left:16px}
.pricing .c-price{padding-left:6px}
.pricing .c-part{padding-left:21px}
.pricing .c-ounce{padding-left:26px}
.pricing tbody tr:nth-child(even){background:var(--row-alt)}
.pricing .col-sep{border-right:1px solid #d8d8d8}
.pricing th.col-sep{border-right:1px solid #6bb9de}
.pricing tbody tr:first-child td{padding-top:10px;height:51px}
.stock{position:absolute;left:98px;top:964px;font-family:"Roboto",sans-serif;font-size:15.5px;color:var(--muted);line-height:31px}
.docs{position:absolute;left:100px;top:1029px;display:flex;gap:12px}
.doc-link{display:flex;align-items:center;justify-content:center;gap:7px;width:172px;height:41px;border:2px solid var(--blue);
  font-family:"Roboto",sans-serif;font-weight:700;font-size:13px;color:var(--blue);text-decoration:none;background:#fff}
.doc-link svg{width:14px;height:17px}
.footer{position:absolute;left:0;top:1133px;width:1025px;height:67px;background:var(--footer);
  font-family:"Roboto",sans-serif;font-size:12.5px;color:#666;text-align:center;line-height:67px}
</style>
</head>
<body>
<div class="page">
  <section class="hero" role="img" aria-label="Soft blurred green background above a pale wooden tabletop"></section>
  <div class="brand"><span class="brand-dot"></span>Harborline</div>

  <h1 class="headline">Isopropyl Alcohol Antiseptic<br>75% Topical Solution<br><span class="accent">Hand Sanitizer</span></h1>

  <ul class="features">
    <li><svg viewBox="0 0 16 16"><circle cx="8" cy="8" r="7" fill="none" stroke="#1693cd" stroke-width="1.4"/><path d="M4.8 8.2l2.2 2.2 4.2-4.4" fill="none" stroke="#1693cd" stroke-width="1.4"/></svg>Active Ingredient 75% Isopropyl Alcohol</li>
    <li><svg viewBox="0 0 16 16"><circle cx="8" cy="8" r="7" fill="none" stroke="#1693cd" stroke-width="1.4"/><path d="M4.8 8.2l2.2 2.2 4.2-4.4" fill="none" stroke="#1693cd" stroke-width="1.4"/></svg>USDA rated E3 hand sanitizer, FDA drug registration<br>number (54555-126)</li>
    <li><svg viewBox="0 0 16 16"><circle cx="8" cy="8" r="7" fill="none" stroke="#1693cd" stroke-width="1.4"/><path d="M4.8 8.2l2.2 2.2 4.2-4.4" fill="none" stroke="#1693cd" stroke-width="1.4"/></svg>Meets World Health Organization (WHO) guidelines for<br>an effective hand sanitizer</li>
    <li><svg viewBox="0 0 16 16"><circle cx="8" cy="8" r="7" fill="none" stroke="#1693cd" stroke-width="1.4"/><path d="M4.8 8.2l2.2 2.2 4.2-4.4" fill="none" stroke="#1693cd" stroke-width="1.4"/></svg>Available in 1, 5, 55 and 275-gallon packages</li>
    <li><svg viewBox="0 0 16 16"><circle cx="8" cy="8" r="7" fill="none" stroke="#1693cd" stroke-width="1.4"/><path d="M4.8 8.2l2.2 2.2 4.2-4.4" fill="none" stroke="#1693cd" stroke-width="1.4"/></svg>Effective on killing germs without drying out your hands</li>
  </ul>

  <div class="product-shot" role="img" aria-label="One-gallon jug of Clendora isopropyl alcohol hand sanitizer"></div>

  <svg class="nav-arrow nav-prev" viewBox="0 0 22 34"><path d="M18 3L5 17l13 14" fill="none" stroke="#777" stroke-width="4"/></svg>
  <svg class="nav-arrow nav-next" viewBox="0 0 22 34"><path d="M4 3l13 14L4 31" fill="none" stroke="#777" stroke-width="4"/></svg>

  <div class="family-photo" role="img" aria-label="Parent in a face mask applying hand sanitizer to a child's hands"></div>

  <table class="pricing">
    <colgroup><col style="width:162px"><col style="width:98px"><col style="width:93px"><col style="width:98px"><col style="width:110px"></colgroup>
    <thead>
      <tr><th class="c-container col-sep">Container</th><th class="c-qty">Min Order<br>Qty</th><th class="c-price col-sep">Price<br>($ per Gallon)</th><th class="c-part col-sep">Part<br>Number</th><th class="c-ounce">Price per<br>Ounce</th></tr>
    </thead>
    <tbody>
      <tr><td class="c-container col-sep">1 Gallon / 4 per case</td><td class="c-qty">48</td><td class="c-price col-sep">$27.92</td><td class="c-part col-sep">IP4148</td><td class="c-ounce">0.218125</td></tr>
      <tr><td class="c-container col-sep">5 Gallon Pail</td><td class="c-qty">36</td><td class="c-price col-sep">$25.86</td><td class="c-part col-sep">IP5400</td><td class="c-ounce">0.202031</td></tr>
      <tr><td class="c-container col-sep">55 Gallon Drum</td><td class="c-qty">4</td><td class="c-price col-sep">$22.42</td><td class="c-part col-sep">IP5540</td><td class="c-ounce">0.175156</td></tr>
      <tr><td class="c-container col-sep">275 Gallon Tote</td><td class="c-qty">1</td><td class="c-price col-sep">$20.24</td><td class="c-part col-sep">IP2751</td><td class="c-ounce">0.158125</td></tr>
    </tbody>
  </table>

  <div class="stock"><p>In Stock Ready to Ship</p><p>Call 555-014-2290 for inquiries</p></div>

  <div class="docs">
    <a class="doc-link" href="#"><svg viewBox="0 0 14 17"><path d="M1 1h8l4 4v11H1z M9 1v4h4" fill="none" stroke="#1693cd" stroke-width="1.4" stroke-linejoin="round"/></svg>Letter of Compliance</a>
    <a class="doc-link" href="#"><svg viewBox="0 0 14 17"><path d="M1 1h8l4 4v11H1z M9 1v4h4" fill="none" stroke="#1693cd" stroke-width="1.4" stroke-linejoin="round"/></svg>Safety Data Sheet</a>
  </div>

  <footer class="footer">© 2020 Company Name | All Rights Reserved</footer>
</div>
</body>
</html>
```